Start-Up für Training, Coaching & Consulting sucht modernes Webdesign!
Zielgruppe
Wer ist TAVI Training, Coaching & Consulting?
Wir führen Führungskräftetrainings durch, machen Privatkunden für Bewerbungen fit und unterstützen Unternehmen mit Verkaufstrainings. Wir entwickeln Persönlichkeiten im Coaching. Wir beraten Unternehmen und helfen ihnen dabei, ihre Geschäftsabläufe und Prozesse zu optimieren. Dabei steht unsere hohe Qualität im Mittelpunkt - gemeinsam mit unseren kreativen Trainingsmethoden. Unser Background (Diplom-Kaufleute und geprüfte Trainer) bietet dafür die passende Ausgangslage.
Was bedeutet TAVI?
Tavi ist Maori und bdeutet Kreis/Spirale. Er symbolisiert einen wachsenden Silberfarn und steht für persönliche Entwicklung und Entfaltung. Der Tavi ist einerseits unser Namensgeber und unser Logo, andererseits steht der Tavi aber auch für unsere Werte: Denn wir wollen unseren Kunden dabei helfen zu wachsen und sich weiterzuentwickeln - und dies auf eine hochqualitative und seriöse Art und Weise ohne den Eindruck von Esoterik oder Erlebnispädagogik zu vermitteln.
Aufgabenstellung
Modernes Design, das unsere Philosophie widerspiegelt: Wir möchten unseren Kunden auf seriöse und hochqualitative Weise weiterentwickeln. Wir stehen für nachhaltigen Lernerfolg, kreative Trainingsmethoden, Abwechslung, Spaß am Lernen, Qualität, Kompetenz, Fachwissen und Dynamik.
Layout:
1) Header: QMSR geprüfter Trainer, Menüpunkte (siehe Architektur)
2) Banner
3) 3 Teaser (Training, Coaching, Consulting) + Header + 2-3 Zeilen Text (+Icons)
>>> Sichtbarer Bereich auf Homepage: Menü, Banner, Teaser
4) "Warum Sie uns wählen sollten": 5 bullet points ohne weiteren Text
5) "Aus unserem Blog": Frame für 3 Blogartikel + Bild + Datum + Header + 2-3 Zeilen Text
6) Alle drei QMSR Logos
7) Footer: Click Us (quick links), Contact Us (Adresse), Follow Us (Pinnwald, ZOLP, Kontaktor)
8) Copyright + Impressum
>>> Das Design soll klar sein, aber nicht zu kantig. Vielmehr sollen abgerundete Ecken und dynamische Elemente genutzt werden.
Architektur:
3 Ebenen:
1) Homepage
2) TAVI, Training, Coaching, Consulting, für Trainer, Kundenstimmen/Referenzen, Kontakt
3) noch zu bestimmende Produktdetailseiten
Texte werden noch erstellt, Layout kann ggf. mit Platzhaltertext gefüllt werden.
Bildmaterial: Logo und vorhandenes Imagebild werden zur Verfügung gestellt. Bilder können ggf. gekauft werden. Vorschläge erwünscht.
Corporate colors:
grün: #a2c61b + monochromatic colors
http://www.tintoskop.de/a2c61b
grau: #474747 + monochromatic colors
http://www.tintoskop.de/474747

```html
<!DOCTYPE html>
<html lang="en">
<head>
<meta charset="utf-8">
<title>TAVI Training, Coaching &amp; Consulting</title>
<link rel="stylesheet" href="https://fonts.googleapis.com/css2?family=Jost:wght@500;600;700&family=Questrial&display=swap">
<style>
:root{
  --green:#a2c61b;
  --green-dark:#7f9c12;
  --grey:#474747;
  --ink:#2b2b2b;
  --nav-bg:#f4f4f4;
  --band-grey:#e2e2e2;
  --footer:#222222;
  --partner-blue:#0a6bbd;
  --white:#ffffff;
}
*{margin:0;padding:0;box-sizing:border-box}
html,body{width:732px;height:1200px;overflow:hidden;background:var(--white)}
body{position:relative;font-family:"Questrial",sans-serif;color:var(--grey)}
.abs{position:absolute}
.top-band{left:0;top:0;width:732px;height:16px;background:var(--green)}
.header{left:0;top:16px;width:732px;height:59px;background:var(--white)}
.brand-box{left:145px;top:0;width:161px;height:75px;background:var(--white);box-shadow:0 0 4px rgba(0,0,0,.12);display:flex;flex-direction:column;align-items:center;justify-content:center}
.brand-name{font-family:"Jost",sans-serif;font-weight:700;font-size:30px;letter-spacing:1px;color:var(--grey);line-height:1}
.brand-rule{width:120px;height:1px;background:var(--green);margin:5px 0 3px}
.brand-tag{font-size:8px;color:var(--grey)}
.brand-tag span{color:var(--green)}
.contact-item{top:36px;display:flex;align-items:center;gap:6px;font-size:9px;color:var(--ink)}
.contact-icon{width:16px;height:16px;border:1px solid var(--green);border-radius:50%;display:flex;align-items:center;justify-content:center}
.nav{left:0;top:75px;width:732px;height:27px;background:var(--nav-bg)}
.nav a{position:absolute;top:10px;font-size:6.5px;color:var(--ink);text-decoration:none}
.hero{left:0;top:102px;width:732px;height:310px;background:radial-gradient(ellipse at 50% 40%,#5d8a2a 0%,#2f5a1b 45%,#17300e 100%)}
.hero-title{left:0;top:193px;width:732px;text-align:center;font-family:"Jost",sans-serif;font-weight:600;font-size:23px;color:var(--white);letter-spacing:.2px}
.hero-title .dot{color:var(--green)}
.hero-text{left:170px;top:230px;width:392px;text-align:center;font-size:7.6px;line-height:14px;color:var(--white)}
.hero-btn{left:307px;top:288px;width:119px;height:22px;background:var(--green);color:var(--white);font-family:"Jost",sans-serif;font-weight:600;font-size:8px;display:flex;align-items:center;justify-content:center}
.hero-arrow{top:241px;width:28px;height:28px;border-radius:50%;background:rgba(0,0,0,.25);display:flex;align-items:center;justify-content:center}
.hero-wave{left:0;top:370px;width:732px;height:50px}
.teaser{top:443px;width:136px;text-align:center}
.teaser-frame{width:136px;height:85px;border:1px solid #dedede;padding:4px;background:var(--white)}
.teaser-photo{width:100%;height:100%}
.teaser-icon{position:absolute;left:52px;top:69px;width:32px;height:32px;border-radius:50%;background:var(--white);border:1px solid var(--green);display:flex;align-items:center;justify-content:center}
.teaser-title{margin-top:21px;font-family:"Jost",sans-serif;font-weight:600;font-size:9px;color:var(--green)}
.teaser-text{margin-top:8px;font-size:6.3px;line-height:11.6px;color:#555}
.teaser-btn{display:inline-block;margin-top:11px;padding:3px 7px;border:1px solid #888;font-family:"Jost",sans-serif;font-weight:600;font-size:5px;color:var(--ink)}
.why{left:0;top:671px;width:732px;height:221px;background:linear-gradient(100deg,#202836 0%,#2c3442 45%,#1d2430 100%)}
.why-notch{left:350px;top:671px;width:33px;height:11px}
.why-title{left:185px;top:764px;font-family:"Jost",sans-serif;font-weight:600;font-size:19.5px;line-height:23px;color:var(--white)}
.why-title span{color:var(--green)}
.why-list{left:362px;top:720px;list-style:none}
.why-list li{display:flex;align-items:center;gap:7px;height:19.8px;font-size:7px;color:var(--white)}
.partners{left:0;top:892px;width:732px;height:160px;background:var(--band-grey)}
.partner-badge{background:var(--partner-blue)}
.footer-wave{left:0;top:1005px;width:732px;height:50px}
.footer{left:0;top:1050px;width:732px;height:123px;background:var(--footer)}
.footer-heading{top:1068px;font-family:"Jost",sans-serif;font-weight:600;font-size:8px;color:var(--white)}
.footer-link{font-size:6.5px;color:var(--white)}
.social{top:1092px;left:324px;display:flex;gap:8px}
.social-item{display:flex;align-items:center;gap:3px;font-size:6.5px;color:var(--white)}
.social-item i{display:block;width:6px;height:6px;background:var(--green)}
.footer-contact{left:458px;font-size:6.5px;line-height:8.5px;color:var(--white);display:flex;gap:7px}
.copyright{left:0;top:1173px;width:732px;height:27px;background:var(--green);color:var(--white);font-size:7px;display:flex;align-items:center;justify-content:center}
</style>
</head>
<body>

<div class="abs header"></div>
<div class="abs top-band"></div>
<div class="abs brand-box">
  <div class="brand-name">TAVI</div>
  <div class="brand-rule"></div>
  <div class="brand-tag">Training <span>•</span> Coaching <span>•</span> Consulting</div>
</div>

<div class="abs contact-item" style="left:373px">
  <span class="contact-icon"><svg width="8" height="6" viewBox="0 0 8 6"><rect x=".5" y=".5" width="7" height="5" fill="none" stroke="#a2c61b"/><path d="M.5 .5 4 3.5 7.5 .5" fill="none" stroke="#a2c61b"/></svg></span>
  info@tavitraining.com
</div>
<div class="abs contact-item" style="left:492px">
  <span class="contact-icon"><svg width="8" height="8" viewBox="0 0 8 8"><path d="M1 1.5c1-1 2 0 2 1L2.3 3.3c.6 1.2 1.3 1.9 2.4 2.4L5.5 5c1 0 2 1 1 2C4 8 0 4 1 1.5z" fill="#a2c61b"/></svg></span>
  604.555.0142 FREE
</div>

<nav class="abs nav">
  <a style="left:151px">Home</a>
  <a style="left:197px">Training</a>
  <a style="left:245px">Coaching</a>
  <a style="left:302px">Consulting</a>
  <a style="left:360px">Products</a>
  <a style="left:412px">Fr Trainer</a>
  <a style="left:464px">Customer Testimonials</a>
  <a style="left:556px">Contact</a>
</nav>

<div class="abs hero" role="img" aria-label="Close-up photo of an unfurling green fern frond"></div>
<h1 class="abs hero-title">TRAINING <span class="dot">•</span> COACHING <span class="dot">•</span> CONSULTING</h1>
<p class="abs hero-text">Lorem ipsum dolor sit amet, consectetur adipisicing elit, sed do eiusmod tempor incididunt ut labore et dolore magna aliqua. Ut enim ad minim veniam, quis nostrud exercitation ullamco laboris nisi ut aliquip ex ea commodo consequat.</p>
<div class="abs hero-btn">GET CONTACT US NOW</div>
<div class="abs hero-arrow" style="left:58px"><svg width="6" height="8" viewBox="0 0 6 8"><path d="M4.5 1 1.5 4l3 3" fill="none" stroke="#fff" stroke-width="1.2"/></svg></div>
<div class="abs hero-arrow" style="left:645px"><svg width="6" height="8" viewBox="0 0 6 8"><path d="M1.5 1l3 3-3 3" fill="none" stroke="#a2c61b" stroke-width="1.2"/></svg></div>
<svg class="abs hero-wave" viewBox="0 0 732 50" preserveAspectRatio="none">
  <path d="M0 23C120 38 200 34 340 20C480 7 620 4 732 21V50H0Z" fill="#fff"/>
  <path d="M0 23C120 38 200 34 340 20C480 7 620 4 732 21V24C620 9 480 12 340 25C200 39 110 41 0 27Z" fill="#a2c61b"/>
</svg>
<svg class="abs" style="left:695px;top:388px" width="36" height="36" viewBox="0 0 36 36"><circle cx="18" cy="18" r="17" fill="#a2c61b"/></svg>

<section>
  <div class="abs teaser" style="left:145px">
    <div class="teaser-frame"><div class="teaser-photo" role="img" aria-label="Photo of a trainer presenting to a seated group in a meeting room" style="background:linear-gradient(120deg,#c9ced6,#6d7a8f 55%,#3f64b8)"></div></div>
    <div class="teaser-icon"><svg width="12" height="12" viewBox="0 0 12 12"><rect x="5" y="1" width="6" height="4" fill="none" stroke="#555"/><circle cx="3" cy="3" r="1.3" fill="#555"/><path d="M1.5 11V6h3v5" fill="none" stroke="#555"/></svg></div>
    <h2 class="teaser-title">TRAINING</h2>
    <p class="teaser-text">This is Photoshop's version of Lorem Ipsum. Proin gravida nibh vel velit auctor aliquet.</p>
    <span class="teaser-btn">READ MORE</span>
  </div>
  <div class="abs teaser" style="left:298px">
    <div class="teaser-frame"><div class="teaser-photo" role="img" aria-label="Photo of a hand drawing a rising glowing line toward a walking figure" style="background:linear-gradient(120deg,#0e2a33,#1d3f4a 50%,#0b1a20)"></div></div>
    <div class="teaser-icon"><svg width="12" height="12" viewBox="0 0 12 12"><circle cx="3" cy="4" r="1.5" fill="#a2c61b"/><circle cx="6" cy="3" r="1.7" fill="#a2c61b"/><circle cx="9" cy="4" r="1.5" fill="#a2c61b"/><path d="M1 9c0-2 10-2 10 0z" fill="#a2c61b"/></svg></div>
    <h2 class="teaser-title">COACHING</h2>
    <p class="teaser-text">This is Photoshop's version of Lorem Ipsum. Proin gravida nibh vel velit auctor aliquet.</p>
    <span class="teaser-btn">READ MORE</span>
  </div>
  <div class="abs teaser" style="left:452px">
    <div class="teaser-frame"><div class="teaser-photo" role="img" aria-label="Photo of two businessmen talking at a desk with a monitor" style="background:linear-gradient(120deg,#e6e9ec,#9aa3ad 45%,#2a3550)"></div></div>
    <div class="teaser-icon"><svg width="12" height="12" viewBox="0 0 12 12"><circle cx="4" cy="5" r="1.8" fill="#555"/><path d="M1 11c0-3 6-3 6 0z" fill="#555"/><rect x="7" y="1" width="4" height="3" rx="1" fill="#555"/></svg></div>
    <h2 class="teaser-title">CONSULTING</h2>
    <p class="teaser-text">This is Photoshop's version of Lorem Ipsum. Proin gravida nibh vel velit auctor aliquet.</p>
    <span class="teaser-btn">READ MORE</span>
  </div>
</section>

<div class="abs why" role="img" aria-label="Dark photo of business people shaking hands across a table"></div>
<svg class="abs why-notch" viewBox="0 0 33 11"><path d="M0 0H33L16.5 11Z" fill="#fff"/></svg>
<h2 class="abs why-title">WHY SHOULD<br><span>CHOOS US</span></h2>
<ul class="abs why-list">
  <li><svg width="8" height="8" viewBox="0 0 8 8"><circle cx="4" cy="4" r="3.5" fill="none" stroke="#fff" stroke-width=".6"/><path d="M3.3 2.5 4.8 4 3.3 5.5" fill="none" stroke="#fff" stroke-width=".6"/></svg>Lorem ipsum dolor sit amet, consectetur adipisicing elit</li>
  <li><svg width="8" height="8" viewBox="0 0 8 8"><circle cx="4" cy="4" r="3.5" fill="none" stroke="#fff" stroke-width=".6"/><path d="M3.3 2.5 4.8 4 3.3 5.5" fill="none" stroke="#fff" stroke-width=".6"/></svg>Sed do eiusmod tempor incididunt ut labore et dolore magna</li>
  <li><svg width="8" height="8" viewBox="0 0 8 8"><circle cx="4" cy="4" r="3.5" fill="none" stroke="#fff" stroke-width=".6"/><path d="M3.3 2.5 4.8 4 3.3 5.5" fill="none" stroke="#fff" stroke-width=".6"/></svg>aliqua. Ut enim ad minim veniam,</li>
  <li><svg width="8" height="8" viewBox="0 0 8 8"><circle cx="4" cy="4" r="3.5" fill="none" stroke="#fff" stroke-width=".6"/><path d="M3.3 2.5 4.8 4 3.3 5.5" fill="none" stroke="#fff" stroke-width=".6"/></svg>Quis nostrud exercitation ullamco laboris nisi ut</li>
  <li><svg width="8" height="8" viewBox="0 0 8 8"><circle cx="4" cy="4" r="3.5" fill="none" stroke="#fff" stroke-width=".6"/><path d="M3.3 2.5 4.8 4 3.3 5.5" fill="none" stroke="#fff" stroke-width=".6"/></svg>Aliquip ex ea commodo consequat.</li>
  <li><svg width="8" height="8" viewBox="0 0 8 8"><circle cx="4" cy="4" r="3.5" fill="none" stroke="#fff" stroke-width=".6"/><path d="M3.3 2.5 4.8 4 3.3 5.5" fill="none" stroke="#fff" stroke-width=".6"/></svg>Duis aute irure dolor in reprehenderit in voluptate velit</li>
  <li><svg width="8" height="8" viewBox="0 0 8 8"><circle cx="4" cy="4" r="3.5" fill="none" stroke="#fff" stroke-width=".6"/><path d="M3.3 2.5 4.8 4 3.3 5.5" fill="none" stroke="#fff" stroke-width=".6"/></svg>Esse cillum dolore eu fugiat nulla pariatur.</li>
</ul>

<div class="abs partners"></div>
<div class="abs partner-badge" role="img" aria-label="Partner membership badge" style="left:158px;top:932px;width:40px;height:52px"></div>
<div class="abs partner-badge" role="img" aria-label="Partner association badge" style="left:300px;top:932px;width:41px;height:53px"></div>
<div class="abs partner-badge" role="img" aria-label="Certified trainer badge" style="left:459px;top:941px;width:116px;height:32px"></div>

<svg class="abs footer-wave" viewBox="0 0 732 50" preserveAspectRatio="none">
  <path d="M0 28C150 16 260 18 400 30C540 42 640 38 732 30V50H0Z" fill="#222"/>
  <path d="M0 26C150 13 260 15 400 27C540 39 640 35 732 26V30C640 38 540 42 400 30C260 18 150 16 0 28Z" fill="#a2c61b"/>
</svg>
<svg class="abs" style="left:8px;top:998px" width="34" height="34" viewBox="0 0 34 34"><circle cx="17" cy="17" r="16" fill="#a2c61b"/></svg>

<footer>
  <div class="abs footer"></div>
  <h3 class="abs footer-heading" style="left:145px">QUICK LINKS</h3>
  <span class="abs footer-link" style="left:145px;top:1094px">Home</span>
  <span class="abs footer-link" style="left:145px;top:1110px">Training</span>
  <span class="abs footer-link" style="left:145px;top:1126px">Coaching</span>
  <span class="abs footer-link" style="left:145px;top:1142px">Consulting</span>
  <span class="abs footer-link" style="left:197px;top:1094px">Products</span>
  <span class="abs footer-link" style="left:197px;top:1110px">Fr Trainer</span>
  <span class="abs footer-link" style="left:197px;top:1126px">Customer Testimonials</span>
  <span class="abs footer-link" style="left:197px;top:1142px">Contact</span>

  <h3 class="abs footer-heading" style="left:324px">FOLLOW US</h3>
  <div class="abs social">
    <span class="social-item"><i></i>Pinnwald</span>
    <span class="social-item"><i></i>ZOLP</span>
    <span class="social-item"><i></i>Kontaktor</span>
  </div>

  <h3 class="abs footer-heading" style="left:458px">CONTACT US</h3>
  <div class="abs footer-contact" style="top:1094px"><svg width="6" height="8" viewBox="0 0 6 8"><path d="M3 8S0 4.5 0 3a3 3 0 0 1 6 0C6 4.5 3 8 3 8z" fill="#fff"/><circle cx="3" cy="3" r="1" fill="#222"/></svg><span>#412, 2280 Linden Street<br>Ashford, BC V0X 2K9</span></div>
  <div class="abs footer-contact" style="top:1120px"><svg width="6" height="6" viewBox="0 0 8 8"><path d="M1 1.5c1-1 2 0 2 1L2.3 3.3c.6 1.2 1.3 1.9 2.4 2.4L5.5 5c1 0 2 1 1 2C4 8 0 4 1 1.5z" fill="#fff"/></svg><span>604.555.0142 FREE</span></div>
  <div class="abs footer-contact" style="top:1135px"><svg width="6" height="5" viewBox="0 0 8 6"><rect width="8" height="6" fill="#fff"/><path d="M0 0 4 3.5 8 0" fill="none" stroke="#222"/></svg><span>info@tavitraining.com</span></div>

  <div class="abs copyright">Tavi © 2015 | All Rights Reserved</div>
</footer>

</body>
</html>
```